verdant terraces simple classy business card design

my name is colin barrow and I run a gardening business aimed at high class verdant terraces. the business name is verdant terraces and our logo was designed on pixel harbour .My clientel are anything from residential homes to businesses. I take pride in my work and know that I offer a service like no other in my area.
The business card will be used to represent my business and I want it to be not only rememberable, but simplistic and modern. Eye catching too. Of course I would like it relatable to gardening and appealing to the correct clientel - those being garden enthusiasts, prestigious homes and businesses that are after top of the line gardening services like no other on the market.
I am not a typical lawn mowing business so I don't want a typical card design that represents that. The gardens I work with are generally million dollar properties with owners who are very garden proud looking for upkeep and guidance from me along with sometimes whole new garden designs. I want the business cards to show to my clients that I take pride, as they do, in their garden. And I want them to know from my card that I am a professional, qualified horticulturist offering them a top of the line service for life. I want them to refer my business on. I want them to look at my business card and see class and professionalism in a modern unique bold way.
The card should be simple with the possibility of the logo on the front being embossed/debossed and my details on the back the card should have a organic garden feel it's very important to me that it is absolutely perfect
I am also very open to ideas and suggestions so look forward to seeing the designs. the business logo has been supplied with this project and I want the card to be double sided

Contact info is
Colin Barrow - Managing Director / Horticulturist
Phone : 0481 526 704
Email: colinbarrow@verdantterraces.example.au

Target Market(s)

high class gardens residential and commercial

Industry/Entity Type

Gardener

Contact Information for Business Card

Contact info is
Phone : 0481 526 704

PLEASE MAKE CARD DOUBLE SIDED

Requirements
Must have
• organic simple classy modern feel
• must flow with the current logo that has been supplied with this project
• Double sided
• Must explain in a simple way that I deal with high end gardens and I'm a qualified horticulturist
Nice to have
• embossed debossed logo
Should not have
• shouldn't be to busy or cheap looking

```html
<!DOCTYPE html>
<html lang="en">
<head>
<meta charset="utf-8">
<title>Verdant Terraces — Business Card</title>
<link href="https://fonts.googleapis.com/css2?family=Arimo:wght@400;700&display=swap" rel="stylesheet">
<style>
  :root {
    --page-bg: #ecebe8;
    --card-paper: #fbfbf9;
    --leaf-green: #4a9a3f;
    --leaf-green-light: #8cc57f;
    --leaf-green-pale: #d6ebcf;
    --ink: #3a3a3a;
    --ink-soft: #555555;
  }
  * { box-sizing: border-box; margin: 0; padding: 0; }
  html, body {
    width: 1200px;
    height: 794px;
    overflow: hidden;
    background: var(--page-bg);
    font-family: "Arimo", Arial, sans-serif;
  }
  .canvas {
    position: relative;
    width: 1200px;
    height: 794px;
  }
  .card {
    position: absolute;
    background: var(--card-paper);
    box-shadow: 0 2px 6px rgba(0,0,0,0.12);
    overflow: hidden;
  }

  /* Front: brand side */
  .card-front {
    left: 109px;
    top: 226px;
    width: 560px;
    height: 342px;
    display: flex;
    flex-direction: column;
    align-items: center;
    justify-content: center;
    gap: 18px;
  }
  .brand-dot {
    width: 64px;
    height: 64px;
    border-radius: 50%;
    background: var(--leaf-green);
  }
  .brand-name {
    color: var(--leaf-green);
    font-weight: 400;
    font-size: 34px;
    letter-spacing: 0.12em;
    text-transform: uppercase;
  }

  /* Back: contact side (portrait) */
  .card-back {
    left: 749px;
    top: 117px;
    width: 342px;
    height: 560px;
  }
  .contact-block {
    position: absolute;
    top: 44px;
    right: 34px;
    text-align: right;
    line-height: 1.45;
  }
  .contact-name {
    color: var(--leaf-green);
    font-weight: 700;
    font-size: 19px;
    letter-spacing: 0.02em;
    text-transform: uppercase;
    margin-bottom: 4px;
  }
  .contact-role {
    color: var(--ink);
    font-size: 13px;
    margin-bottom: 6px;
  }
  .contact-line {
    color: var(--ink-soft);
    font-size: 12px;
  }
  .contact-label { color: var(--leaf-green); }

  .tree-artwork {
    position: absolute;
    left: 40px;
    top: 190px;
    width: 262px;
    height: 300px;
    border-radius: 50% 50% 40% 40%;
    background: radial-gradient(circle at 50% 40%, var(--leaf-green-light), var(--leaf-green-pale) 75%);
  }
  .ground-band {
    position: absolute;
    left: 0;
    bottom: 0;
    width: 100%;
    height: 38px;
    background: var(--leaf-green);
  }
  .ground-band::after {
    content: "";
    position: absolute;
    left: 0;
    right: 0;
    top: 9px;
    height: 1px;
    background: rgba(255,255,255,0.7);
  }
</style>
</head>
<body>
  <main class="canvas">
    <section class="card card-front" aria-label="Card front">
      <div class="brand-dot"></div>
      <div class="brand-name">Verdant Terraces</div>
    </section>

    <section class="card card-back" aria-label="Card back">
      <div class="contact-block">
        <div class="contact-name">Colin Barrow</div>
        <div class="contact-role">Managing Director / Horticulturist</div>
        <div class="contact-line"><span class="contact-label">P :</span> 0481 526 704</div>
        <div class="contact-line">colinbarrow@verdantterraces.example.au</div>
        <div class="contact-line">verdantterraces.example.au</div>
      </div>
      <div class="tree-artwork" role="img" aria-label="Green leafy tree illustration growing from the ground band"></div>
      <div class="ground-band"></div>
    </section>
  </main>
</body>
</html>
```